PowerPoint Design for upcoming Broadcast

I need a PowerPoint design complete with all the templates in PPT, i.e two columns of text, one column of text with adjacent area for image, etc. Per the attached logo. Do not use the gold element in the design. 16x9

Target Market(s)

Business Leaders

Industry/Entity Type

Business Consultant

Other font styles liked:
• Arial

Colors

Designer to choose colors to be used in the design.

Requirements
Must have
• Crisp clean design. #for each color used.
Nice to have
• An assortment of charts in the ppt color schemes. A military (KVTF) theme.
Should not have
• Gaudy. Flashy. Transitions.

```html
<!DOCTYPE html>
<html lang="en">
<head>
<meta charset="utf-8">
<title>Steadfast Line Leadership – Presentation Template Set</title>
<link href="https://fonts.googleapis.com/css2?family=Arimo:wght@400;700&display=swap" rel="stylesheet">
<style>
:root{
  --red:#c41230;
  --red-deep:#8e0d22;
  --ink:#161616;
  --gold:#b39056;
  --rule:#cfcfcf;
  --paper:#ffffff;
  --canvas:#e8e8e8;
  --muted:#444444;
  --soft:#c9c9c9;
}
*{box-sizing:border-box;margin:0;padding:0}
html,body{width:1200px;height:1028px;overflow:hidden}
body{background:var(--canvas);font-family:'Arimo',Arial,sans-serif;color:var(--ink)}
h2{font-weight:400}
.deck{display:grid;grid-template-columns:repeat(5,222px);grid-auto-rows:125px;column-gap:14.5px;row-gap:14.8px;padding:31px 18px}
.slide{position:relative;overflow:hidden;background:var(--paper)}
.slide.dark{background:var(--ink);color:#fff}
.abs{position:absolute}
.photo{position:absolute}
.title{position:absolute;left:7px;top:6px;right:24px;font-size:7px;font-weight:400;padding-bottom:2px;border-bottom:.5px solid var(--rule)}
.dark .title{border-bottom-color:#444}
.mark{position:absolute;right:6px;top:5px;width:12px;height:12px;border-radius:50%;background:var(--red);border:1px solid var(--ink)}
.dark .mark{border-color:#000}
.foot{position:absolute;left:0;right:0;bottom:0;height:5px;background:var(--ink);color:#fff;font-size:2.6px;line-height:5px;padding-left:6px;letter-spacing:.1px}
.dark .foot{background:transparent;border-top:.4px solid #333}
.foot b{position:absolute;right:6px;top:0;height:5px;width:16px;background:var(--red);font-weight:400;text-align:center}
.txt{font-size:3.3px;line-height:1.4;color:var(--muted);font-weight:400}
.dark .txt{color:var(--soft)}
.red{color:var(--red)}
.dot{position:absolute;width:7px;height:7px;border-radius:50%;background:var(--red)}
.ring{position:absolute;width:8px;height:8px;border-radius:50%;border:.6px solid #ddd}
.brand{font-size:6.5px;letter-spacing:.2px;text-align:center;font-weight:400}
.sub{font-size:4.6px;line-height:1.3;text-align:center;font-weight:400}
.quote{font-size:13px;font-weight:700;color:var(--red);line-height:1}
.num{font-size:9px;width:8px;text-align:right}
.bar{border-left:.8px solid var(--red);padding-left:3px}
.seal{border-radius:50%;background:var(--red)}
.key{display:inline-block;width:4px;height:4px;margin-right:3px}
</style>
</head>
<body>
<main class="deck">

<section class="slide dark">
  <div class="photo" style="left:0;top:0;width:72px;height:125px;background:linear-gradient(90deg,#2b2b2b,#151515)" role="img" aria-label="Business leader in a dark suit"></div>
  <div class="photo" style="right:0;top:0;width:62px;height:125px;background:linear-gradient(270deg,#3a2020,#151515)" role="img" aria-label="Officer in dress uniform"></div>
  <div class="abs seal" style="left:105px;top:16px;width:13px;height:13px"></div>
  <p class="abs brand" style="left:50px;width:122px;top:35px">STEADFAST LINE LEADERSHIP</p>
  <p class="abs sub" style="left:52px;width:118px;top:72px">Developing Entrepreneurial Leaders and Winning the Small Business War</p>
</section>

<section class="slide dark">
  <div class="photo" style="left:0;top:0;width:78px;height:125px;background:linear-gradient(90deg,#2b2b2b,#151515)" role="img" aria-label="Business leader in a dark suit"></div>
  <div class="abs seal" style="left:72px;top:38px;width:12px;height:12px"></div>
  <p class="abs brand" style="left:88px;top:42px;text-align:left">STEADFAST LINE LEADERSHIP</p>
  <p class="abs sub" style="left:93px;width:118px;top:57px">Developing Entrepreneurial Leaders and Winning the Small Business War</p>
  <div class="abs" style="left:135px;top:76px;width:32px;height:.8px;background:var(--red)"></div>
</section>

<section class="slide dark">
  <div class="photo" style="right:0;top:0;width:60px;height:125px;background:linear-gradient(270deg,#3a2020,#151515)" role="img" aria-label="Officer in dress uniform"></div>
  <div class="abs seal" style="left:72px;top:38px;width:12px;height:12px"></div>
  <p class="abs brand" style="left:88px;top:42px;text-align:left">STEADFAST LINE LEADERSHIP</p>
  <p class="abs sub" style="left:93px;width:118px;top:57px">Developing Entrepreneurial Leaders and Winning the Small Business War</p>
  <div class="abs" style="left:135px;top:76px;width:32px;height:.8px;background:var(--red)"></div>
</section>

<section class="slide dark" style="background:linear-gradient(180deg,#1b1b1b,#101010)">
  <p class="abs quote" style="left:40px;top:38px">&ldquo;</p>
  <p class="abs txt" style="left:54px;top:46px;width:112px">Lorem ipsum dolor sit amet, consectetur adipiscing elit, sed do eiusmod tempor incididunt ut labore et dolore magna aliqua. Ut enim ad minim veniam, quis nostrud exercitation ullamco laboris nisi ut aliquip ex ea commodo consequat.</p>
  <p class="abs quote" style="left:168px;top:62px">&rdquo;</p>
  <footer class="foot">STEADFAST LINE LEADERSHIP<b>Page 4</b></footer>
</section>

<section class="slide dark">
  <div class="photo" style="inset:0;background:linear-gradient(180deg,#262626,#111)" role="img" aria-label="Dim boardroom interior"></div>
  <div class="abs seal" style="left:104px;top:16px;width:14px;height:14px"></div>
  <p class="abs brand" style="left:0;width:222px;top:48px">WELCOME MESSAGE</p>
  <p class="abs txt" style="left:58px;top:66px;width:110px">Lorem ipsum dolor sit amet, consectetur adipiscing elit, sed do eiusmod tempor incididunt ut labore et dolore magna aliqua. Ut enim ad minim veniam, quis nostrud exercitation ullamco laboris nisi ut aliquip ex ea commodo consequat.</p>
  <footer class="foot">STEADFAST LINE LEADERSHIP<b>Page 5</b></footer>
</section>

<section class="slide">
  <div class="abs seal" style="left:104px;top:17px;width:14px;height:14px;border:1px solid var(--ink)"></div>
  <p class="abs brand red" style="left:0;width:222px;top:47px">WELCOME MESSAGE</p>
  <p class="abs quote" style="left:42px;top:60px;font-size:10px">&ldquo;</p>
  <p class="abs txt" style="left:58px;top:66px;width:108px">Lorem ipsum dolor sit amet, consectetur adipiscing elit, sed do eiusmod tempor incididunt ut labore et dolore magna aliqua. Ut enim ad minim veniam, quis nostrud exercitation ullamco laboris nisi ut aliquip ex ea commodo consequat.</p>
  <p class="abs quote" style="left:170px;top:80px;font-size:10px">&rdquo;</p>
  <footer class="foot">STEADFAST LINE LEADERSHIP<b>Page 6</b></footer>
</section>

<section class="slide">
  <h2 class="title">Agenda</h2><div class="mark"></div>
  <div class="abs" style="left:40px;top:32px;display:grid;grid-template-columns:78px 78px;row-gap:11px;column-gap:8px">
    <div style="display:flex;gap:3px;align-items:center"><span class="num">1</span><p class="txt bar">Lorem ipsum dolor sit amet, consectetur adipiscing elit</p></div>
    <div style="display:flex;gap:3px;align-items:center"><span class="num">4</span><p class="txt bar">Lorem ipsum dolor sit amet, consectetur adipiscing elit</p></div>
    <div style="display:flex;gap:3px;align-items:center"><span class="num">2</span><p class="txt bar">Lorem ipsum dolor sit amet, consectetur adipiscing elit</p></div>
    <div style="display:flex;gap:3px;align-items:center"><span class="num">5</span><p class="txt bar">Lorem ipsum dolor sit amet, consectetur adipiscing elit</p></div>
    <div style="display:flex;gap:3px;align-items:center"><span class="num">3</span><p class="txt bar">Lorem ipsum dolor sit amet, consectetur adipiscing elit</p></div>
    <div style="display:flex;gap:3px;align-items:center"><span class="num">6</span><p class="txt bar">Lorem ipsum dolor sit amet, consectetur adipiscing elit</p></div>
  </div>
  <footer class="foot">STEADFAST LINE LEADERSHIP<b>Page 7</b></footer>
</section>

<section class="slide">
  <div class="photo" style="left:0;top:0;width:112px;height:125px;background:linear-gradient(180deg,#e2e2e2,#8c8c8c 60%,#5a5a5a)" role="img" aria-label="Laptop on a desk in front of a city skyline"></div>
  <h2 class="abs" style="left:7px;top:6px;font-size:7px">Agenda</h2>
  <div class="abs" style="left:112px;top:0;width:110px;height:125px;background:var(--ink)"></div>
  <div class="mark"></div>
  <div class="abs" style="left:120px;top:20px;display:grid;row-gap:8px;color:#fff">
    <div style="display:flex;gap:4px;align-items:center"><span class="num">1</span><p class="txt bar" style="color:#ccc">Lorem ipsum dolor sit amet, consectetur adipiscing elit</p></div>
    <div style="display:flex;gap:4px;align-items:center"><span class="num">2</span><p class="txt bar" style="color:#ccc">Lorem ipsum dolor sit amet, consectetur adipiscing elit</p></div>
    <div style="display:flex;gap:4px;align-items:center"><span class="num">3</span><p class="txt bar" style="color:#ccc">Lorem ipsum dolor sit amet, consectetur adipiscing elit</p></div>
    <div style="display:flex;gap:4px;align-items:center"><span class="num">4</span><p class="txt bar" style="color:#ccc">Lorem ipsum dolor sit amet, consectetur adipiscing elit</p></div>
    <div style="display:flex;gap:4px;align-items:center"><span class="num">5</span><p class="txt bar" style="color:#ccc">Lorem ipsum dolor sit amet, consectetur adipiscing elit</p></div>
  </div>
  <footer class="foot">STEADFAST LINE LEADERSHIP<b>Page 8</b></footer>
</section>

<section class="slide dark">
  <div class="photo" style="left:0;top:0;width:72px;height:125px;background:linear-gradient(90deg,#3a2020,#151515)" role="img" aria-label="Officer in dress uniform"></div>
  <h2 class="abs" style="left:74px;top:10px;font-size:7px">About Us</h2><div class="mark"></div>
  <div class="abs" style="left:74px;top:20px;width:136px;height:.5px;background:#444"></div>
  <p class="abs txt" style="left:74px;top:40px;width:112px">Lorem ipsum dolor sit amet, consectetur adipiscing elit, sed do eiusmod tempor incididunt ut labore et dolore magna aliqua. Ut enim ad minim veniam, quis nostrud exercitation ullamco laboris nisi ut aliquip ex ea commodo consequat.<br><br>Duis aute irure dolor in reprehenderit in voluptate velit esse cillum dolore eu fugiat nulla pariatur. Excepteur sint occaecat cupidatat non proident, sunt in culpa qui officia deserunt mollit anim id est laborum.</p>
  <footer class="foot">STEADFAST LINE LEADERSHIP<b>Page 9</b></footer>
</section>

<section class="slide dark">
  <div class="photo" style="left:0;top:0;width:72px;height:125px;background:linear-gradient(90deg,#2d2d2d,#151515)" role="img" aria-label="Business leader in a dark suit"></div>
  <h2 class="abs" style="left:74px;top:10px;font-size:7px">About Us</h2><div class="mark"></div>
  <div class="abs" style="left:74px;top:20px;width:136px;height:.5px;background:#444"></div>
  <p class="abs txt" style="left:74px;top:30px;width:112px">Lorem ipsum dolor sit amet, consectetur adipiscing elit, sed do eiusmod tempor incididunt ut labore et dolore magna aliqua. Ut enim ad minim veniam, quis nostrud exercitation ullamco laboris nisi ut aliquip ex ea commodo consequat.<br><br>Duis aute irure dolor in reprehenderit in voluptate velit esse cillum dolore eu fugiat nulla pariatur. Excepteur sint occaecat cupidatat non proident, sunt in culpa qui officia deserunt mollit anim id est laborum.</p>
  <footer class="foot">STEADFAST LINE LEADERSHIP<b>Page 10</b></footer>
</section>

<section class="slide dark">
  <div class="photo" style="inset:0;background:linear-gradient(160deg,#3a2418,#1a1210 60%,#0e0e0e)" role="img" aria-label="Dark sky over a memorial"></div>
  <h2 class="title">Mission, Vision and Values</h2><div class="mark"></div>
  <div class="dot" style="left:72px;top:34px"></div>
  <p class="abs txt" style="left:86px;top:33px;width:106px">Our mission is &ldquo;Developing Entrepreneurial Leaders and Winning the Small Business War.&rdquo;</p>
  <div class="dot" style="left:72px;top:61px"></div>
  <p class="abs txt" style="left:86px;top:57px;width:110px">Our vision is to become the premier entrepreneurial leadership development firm in the world by helping business owners successfully start, grow and create wealth through a defined business doctrine.</p>
  <div class="dot" style="left:72px;top:92px"></div>
  <p class="abs txt" style="left:86px;top:89px;width:110px">Our values are embodied by our name &ndash; Steadfast Line &ndash; our promise to stay faithful. Honor, Courage &amp; Commitment.</p>
  <footer class="foot">STEADFAST LINE LEADERSHIP<b>Page 11</b></footer>
</section>

<section class="slide dark">
  <div class="photo" style="inset:0;background:linear-gradient(160deg,#3a2418,#1a1210 60%,#0e0e0e)" role="img" aria-label="Dark sky over a memorial"></div>
  <h2 class="title">Mission, Vision and Values</h2><div class="mark"></div>
  <div class="ring" style="left:70px;top:33px"></div>
  <p class="abs txt" style="left:86px;top:33px;width:106px">Our mission is &ldquo;Developing Entrepreneurial Leaders and Winning the Small Business War.&rdquo;</p>
  <div class="ring" style="left:70px;top:62px"></div>
  <p class="abs txt" style="left:86px;top:57px;width:110px">Our vision is to become the premier entrepreneurial leadership development firm in the world by helping business owners successfully start, grow and create wealth through a defined business doctrine.</p>
  <div class="ring" style="left:70px;top:92px"></div>
  <p class="abs txt" style="left:86px;top:89px;width:110px">Our values are embodied by our name &ndash; Steadfast Line &ndash; our promise to stay faithful. Honor, Courage &amp; Commitment.</p>
  <footer class="foot">STEADFAST LINE LEADERSHIP<b>Page 12</b></footer>
</section>

<section class="slide dark">
  <div class="photo" style="left:0;top:0;width:112px;height:125px;background:linear-gradient(180deg,#2a2018,#6e5638 60%,#2a2016)" role="img" aria-label="Bronze memorial statue with a flag"></div>
  <h2 class="abs" style="left:7px;top:8px;font-size:7px">Mission, Vision and Values</h2><div class="mark"></div>
  <div class="abs" style="left:112px;top:0;width:110px;height:125px;background:rgba(20,20,20,.92)"></div>
  <div class="ring" style="left:115px;top:30px"></div>
  <p class="abs txt" style="left:128px;top:28px;width:84px">Our mission is &ldquo;Developing Entrepreneurial Leaders and Winning the Small Business War.&rdquo;</p>
  <div class="ring" style="left:115px;top:60px"></div>
  <p class="abs txt" style="left:128px;top:52px;width:86px">Our vision is to become the premier entrepreneurial leadership firm in the world by helping owners start, grow and create wealth.</p>
  <div class="ring" style="left:115px;top:92px"></div>
  <p class="abs txt" style="left:128px;top:87px;width:86px">Our values are embodied by our name &ndash; Steadfast Line. Honor, Courage &amp; Commitment.</p>
  <footer class="foot">STEADFAST LINE LEADERSHIP<b>Page 13</b></footer>
</section>

<section class="slide">
  <h2 class="title">Mission, Vision &amp; Values</h2><div class="mark"></div>
  <p class="abs" style="left:158px;top:11px;font-size:2.6px;color:#555">Red 8F050B<br>AE3B36</p>
  <div class="dot" style="left:48px;top:34px"></div>
  <p class="abs txt" style="left:66px;top:33px;width:112px">Our mission is &ldquo;Developing Entrepreneurial Leaders and Winning the Small Business War.&rdquo;</p>
  <div class="dot" style="left:48px;top:63px"></div>
  <p class="abs txt" style="left:66px;top:58px;width:118px">Our vision is to become the premier entrepreneurial leadership development firm in the world by helping business owners successfully start, grow and create wealth through a defined business doctrine.</p>
  <div class="dot" style="left:48px;top:94px"></div>
  <p class="abs txt" style="left:66px;top:91px;width:112px">Our values are embodied by our name &ndash; Steadfast Line. Honor, Courage &amp; Commitment.</p>
  <footer class="foot">STEADFAST LINE LEADERSHIP<b>Page 14</b></footer>
</section>

<section class="slide">
  <h2 class="title">Mission, Vision &amp; Values</h2><div class="mark"></div>
  <p class="abs" style="left:158px;top:11px;font-size:2.6px;color:#555">Red 8F050B</p>
  <div class="dot" style="left:48px;top:34px"></div>
  <p class="abs txt" style="left:66px;top:33px;width:112px">Our <span class="red">MISSION</span> is &ldquo;Developing Entrepreneurial Leaders and Winning the Small Business War.&rdquo;</p>
  <div class="dot" style="left:48px;top:63px"></div>
  <p class="abs txt" style="left:66px;top:58px;width:118px">Our <span class="red">VISION</span> is to become the premier entrepreneurial leadership development firm in the world by helping business owners successfully start, grow and create wealth through a defined business doctrine.</p>
  <div class="dot" style="left:48px;top:94px"></div>
  <p class="abs txt" style="left:66px;top:91px;width:112px">Our <span class="red">VALUES</span> are embodied by our name &ndash; Steadfast Line. Honor, Courage &amp; Commitment.</p>
  <footer class="foot">STEADFAST LINE LEADERSHIP<b>Page 15</b></footer>
</section>

<section class="slide">
  <h2 class="title">Mission, Vision &amp; Values</h2><div class="mark"></div>
  <p class="abs" style="left:158px;top:11px;font-size:2.6px;color:#555">Red 8F050B</p>
  <svg class="abs" style="left:16px;top:34px" width="60" height="60" viewBox="0 0 60 60">
    <circle cx="30" cy="20" r="17" fill="var(--red)" opacity=".95"/>
    <circle cx="19" cy="38" r="17" fill="var(--ink)" opacity=".9"/>
    <circle cx="41" cy="38" r="17" fill="var(--gold)" opacity=".85"/>
    <circle cx="30" cy="32" r="4" fill="#fff"/>
  </svg>
  <p class="abs txt" style="left:100px;top:33px;width:100px">Our mission is &ldquo;Developing Entrepreneurial Leaders and Winning the Small Business War.&rdquo;</p>
  <p class="abs txt" style="left:100px;top:54px;width:104px">Our vision is to become the premier entrepreneurial leadership development firm in the world by helping business owners start, grow and create wealth through a defined doctrine.</p>
  <p class="abs txt" style="left:100px;top:86px;width:100px">Our values are embodied by our name &ndash; Steadfast Line. Honor, Courage &amp; Commitment.</p>
  <footer class="foot">STEADFAST LINE LEADERSHIP<b>Page 16</b></footer>
</section>

<section class="slide">
  <h2 class="title">Advisory Board</h2><div class="mark"></div>
  <p class="abs txt" style="left:30px;top:26px;color:var(--ink)">Steadfast Line Leadership&trade; Institute Advisory Board</p>
  <div class="abs seal" style="left:28px;top:40px;width:18px;height:18px;background:#9a9a9a" role="img" aria-label="Portrait of Thomas R. Hale"></div>
  <p class="abs txt" style="left:50px;top:41px;width:58px"><span class="red">Major General Thomas R. Hale, KVTF (Ret)</span><br>Commanding General of the 2nd Field Command</p>
  <div class="abs seal" style="left:122px;top:40px;width:18px;height:18px;background:#7d7d7d" role="img" aria-label="Portrait of Carl D. Benning"></div>
  <p class="abs txt" style="left:144px;top:41px;width:58px"><span class="red">Carl D. Benning</span><br>Founder and Chief Warfighting Officer of the Steadfast Line Institute</p>
  <div class="abs seal" style="left:28px;top:74px;width:18px;height:18px;background:#a4a4a4" role="img" aria-label="Portrait of Martin P. Rowe"></div>
  <p class="abs txt" style="left:50px;top:75px;width:58px"><span class="red">Martin P. Rowe</span><br>High-technology industry executive and successful entrepreneur for 40 years</p>
  <div class="abs seal" style="left:122px;top:74px;width:18px;height:18px;background:#8a8a8a" role="img" aria-label="Portrait of Paul H. Arden"></div>
  <p class="abs txt" style="left:144px;top:75px;width:58px"><span class="red">Paul H. Arden</span><br>CEO of Northgate Growth Partners</p>
  <footer class="foot">STEADFAST LINE LEADERSHIP<b>Page 17</b></footer>
</section>

<section class="slide">
  <h2 class="title">Product and Services</h2><div class="mark"></div>
  <svg class="abs" style="left:82px;top:30px" width="58" height="58" viewBox="0 0 58 58">
    <circle cx="29" cy="29" r="28" fill="var(--red)"/>
    <path d="M29 29 L1 29 A28 28 0 0 0 29 57 Z" fill="var(--gold)"/>
    <path d="M29 29 L57 29 A28 28 0 0 0 29 1 Z" fill="var(--gold)"/>
    <circle cx="29" cy="29" r="8" fill="#fff"/>
    <circle cx="29" cy="29" r="5" fill="var(--red)"/>
    <circle cx="15" cy="17" r="5" fill="var(--ink)"/><circle cx="43" cy="17" r="5" fill="var(--ink)"/>
    <circle cx="15" cy="41" r="5" fill="var(--ink)"/><circle cx="43" cy="41" r="5" fill="var(--ink)"/>
  </svg>
  <p class="abs txt" style="left:16px;top:38px;width:60px"><span class="red">Small business consulting</span><br>Steadfast Line Leadership works with entrepreneurs and small business owners to develop leaders within your company.</p>
  <p class="abs txt" style="left:16px;top:74px;width:60px"><span class="red">Books</span><br>Leadership is learned. This book quantifies the key behaviors needed to reach that goal.</p>
  <p class="abs txt" style="left:148px;top:36px;width:62px"><span class="red">Capital</span><br>You can have the greatest products and services, greatest leadership and wealth, but still need capital.</p>
  <p class="abs txt" style="left:148px;top:72px;width:62px"><span class="red">Field Guide 365&trade;</span><br>A pocket training tool in a teachable moment. Includes more than 365 individual training modules.</p>
  <footer class="foot">STEADFAST LINE LEADERSHIP<b>Page 18</b></footer>
</section>

<section class="slide">
  <h2 class="title">Product and Services</h2><div class="mark"></div>
  <div class="dot" style="left:28px;top:33px"></div>
  <p class="abs txt" style="left:38px;top:32px;width:62px"><span class="red">Small business consulting</span><br>Steadfast Line Leadership works with entrepreneurs and small business owners to develop leaders within your company.</p>
  <div class="dot" style="left:115px;top:33px;background:var(--ink)"></div>
  <p class="abs txt" style="left:125px;top:32px;width:66px">Capital<br>You can have the greatest products and services, greatest leadership and wealth, but still need capital to grow.</p>
  <div class="dot" style="left:28px;top:71px;background:var(--ink)"></div>
  <p class="abs txt" style="left:38px;top:70px;width:62px">Books<br>Leadership is learned. This book quantifies the key behaviors needed to reach the goal of becoming an outstanding leader.</p>
  <div class="dot" style="left:115px;top:71px"></div>
  <p class="abs txt" style="left:125px;top:70px;width:66px"><span class="red">Field Guide 365&trade;</span><br>A pocket training tool in a teachable moment. Includes more than 365 individual training modules.</p>
  <footer class="foot">STEADFAST LINE LEADERSHIP<b>Page 19</b></footer>
</section>

<section class="slide">
  <h2 class="title">Product and Services</h2><div class="mark"></div>
  <div class="dot" style="left:28px;top:28px"></div>
  <p class="abs txt" style="left:40px;top:27px;width:160px"><span class="red">Small business consulting</span><br>Steadfast Line Leadership works with entrepreneurs and small business owners to develop leaders within your company.</p>
  <div class="dot" style="left:28px;top:48px;background:var(--ink)"></div>
  <p class="abs txt" style="left:40px;top:47px;width:160px">Capital<br>You can have the greatest products and services, greatest leadership and wealth, but you still need capital to grow.</p>
  <div class="dot" style="left:28px;top:67px"></div>
  <p class="abs txt" style="left:40px;top:66px;width:160px"><span class="red">Books</span><br>Leadership is learned. This book quantifies the key behaviors needed to become an outstanding leader.</p>
  <div class="dot" style="left:28px;top:87px;background:var(--ink)"></div>
  <p class="abs txt" style="left:40px;top:86px;width:160px">Field Guide 365&trade;<br>A pocket training tool in a teachable moment. Includes more than 365 individual training modules.</p>
  <footer class="foot">STEADFAST LINE LEADERSHIP<b>Page 20</b></footer>
</section>

<section class="slide">
  <h2 class="title">Table</h2><div class="mark"></div>
  <div class="abs" style="left:8px;top:30px;display:grid;grid-template-columns:repeat(4,45px);column-gap:3.5px">
    <div style="border:.5px solid #bbb;height:78px;text-align:center"><p style="background:var(--ink);color:#fff;font-size:7px;padding:4px 0">$111</p><p class="red" style="font-size:4px;margin:4px 0">LOREM IPSUM</p><p class="txt" style="padding:4px 3px;border-top:.5px solid #ddd">Steadfast Line works with entrepreneurs to develop leaders within your company.</p></div>
    <div style="border:.5px solid #bbb;height:78px;text-align:center"><p style="background:var(--ink);color:#fff;font-size:7px;padding:4px 0">$111</p><p class="red" style="font-size:4px;margin:4px 0">LOREM IPSUM</p><p class="txt" style="padding:4px 3px;border-top:.5px solid #ddd">Steadfast Line works with entrepreneurs to develop leaders within your company.</p></div>
    <div style="border:.5px solid #bbb;height:78px;text-align:center"><p style="background:var(--ink);color:#fff;font-size:7px;padding:4px 0">$111</p><p class="red" style="font-size:4px;margin:4px 0">LOREM IPSUM</p><p class="txt" style="padding:4px 3px;border-top:.5px solid #ddd">Steadfast Line works with entrepreneurs to develop leaders within your company.</p></div>
    <div style="border:.5px solid #bbb;height:78px;text-align:center"><p style="background:var(--ink);color:#fff;font-size:7px;padding:4px 0">$111</p><p class="red" style="font-size:4px;margin:4px 0">LOREM IPSUM</p><p class="txt" style="padding:4px 3px;border-top:.5px solid #ddd">Steadfast Line works with entrepreneurs to develop leaders within your company.</p></div>
  </div>
  <footer class="foot">STEADFAST LINE LEADERSHIP<b>Page 21</b></footer>
</section>

<section class="slide">
  <h2 class="title">Timeline History</h2><div class="mark"></div>
  <svg class="abs" style="left:0;top:0" width="222" height="125" viewBox="0 0 222 125">
    <line x1="6" y1="70" x2="222" y2="70" stroke="var(--ink)" stroke-width="1"/>
    <polygon points="222,70 216,67 216,73" fill="var(--ink)"/>
    <g fill="#777"><circle cx="32" cy="70" r="3"/><circle cx="68" cy="70" r="3"/><circle cx="104" cy="70" r="3"/><circle cx="140" cy="70" r="3"/><circle cx="176" cy="70" r="3"/></g>
    <g stroke="var(--red)" stroke-width=".5" stroke-dasharray="1 1"><line x1="32" y1="62" x2="32" y2="48"/><line x1="104" y1="62" x2="104" y2="48"/><line x1="176" y1="62" x2="176" y2="48"/><line x1="68" y1="78" x2="68" y2="92"/><line x1="140" y1="78" x2="140" y2="92"/></g>
    <g font-size="5" fill="var(--ink)" font-family="Arimo, Arial, sans-serif" text-anchor="middle"><text x="32" y="82">2014</text><text x="68" y="62">2015</text><text x="104" y="82">2016</text><text x="140" y="62">2017</text><text x="176" y="82">2018</text></g>
  </svg>
  <p class="abs txt" style="left:8px;top:26px;width:48px;text-align:center">Lorem ipsum dolor sit amet, consectetur adipiscing elit, sed do eiusmod tempor incididunt.</p>
  <p class="abs txt" style="left:80px;top:26px;width:48px;text-align:center">Lorem ipsum dolor sit amet, consectetur adipiscing elit, sed do eiusmod tempor incididunt.</p>
  <p class="abs txt" style="left:152px;top:26px;width:48px;text-align:center">Lorem ipsum dolor sit amet, consectetur adipiscing elit, sed do eiusmod tempor incididunt.</p>
  <p class="abs txt" style="left:44px;top:94px;width:48px;text-align:center">Lorem ipsum dolor sit amet, consectetur adipiscing elit, sed do eiusmod.</p>
  <p class="abs txt" style="left:116px;top:94px;width:48px;text-align:center">Lorem ipsum dolor sit amet, consectetur adipiscing elit, sed do eiusmod.</p>
  <footer class="foot">STEADFAST LINE LEADERSHIP<b>Page 22</b></footer>
</section>

<section class="slide">
  <h2 class="title">Column Text</h2><div class="mark"></div>
  <p class="abs red" style="left:26px;top:24px;font-size:4.6px">Lorem ipsum dolor sit amet, consectetur adipiscing elit</p>
  <div class="abs" style="left:26px;top:36px;display:grid;grid-template-columns:repeat(3,54px);column-gap:11px">
    <p class="txt">Lorem ipsum dolor sit amet, consectetur adipiscing elit, sed do eiusmod tempor incididunt ut labore et dolore magna aliqua. Ut enim ad minim veniam, quis nostrud exercitation ullamco laboris nisi ut aliquip ex ea commodo consequat.<br><br>Duis aute irure dolor in reprehenderit in voluptate velit esse cillum dolore eu fugiat nulla pariatur.</p>
    <p class="txt">Lorem ipsum dolor sit amet, consectetur adipiscing elit, sed do eiusmod tempor incididunt ut labore et dolore magna aliqua. Ut enim ad minim veniam, quis nostrud exercitation ullamco laboris nisi ut aliquip ex ea commodo consequat.<br><br>Duis aute irure dolor in reprehenderit in voluptate velit esse cillum dolore eu fugiat nulla pariatur.</p>
    <p class="txt">Lorem ipsum dolor sit amet, consectetur adipiscing elit, sed do eiusmod tempor incididunt ut labore et dolore magna aliqua. Ut enim ad minim veniam, quis nostrud exercitation ullamco laboris nisi ut aliquip ex ea commodo consequat.<br><br>Duis aute irure dolor in reprehenderit in voluptate velit esse cillum dolore eu fugiat nulla pariatur.</p>
  </div>
  <footer class="foot">STEADFAST LINE LEADERSHIP<b>Page 23</b></footer>
</section>

<section class="slide">
  <h2 class="title">Column Text</h2><div class="mark"></div>
  <p class="abs" style="left:32px;top:28px;width:158px;background:var(--red);color:#fff;font-size:3.6px;line-height:1.35;padding:1.5px 2px">Lorem ipsum dolor sit amet, consectetur adipiscing elit, sed do eiusmod tempor incididunt ut labore et dolore magna aliqua. Ut enim ad minim veniam, quis nostrud exercitation ullamco laboris nisi ut aliquip ex ea commodo consequat.</p>
  <div class="abs" style="left:32px;top:52px;display:grid;grid-template-columns:74px 74px;column-gap:10px">
    <p class="txt">Lorem ipsum dolor sit amet, consectetur adipiscing elit, sed do eiusmod tempor incididunt ut labore et dolore magna aliqua. Ut enim ad minim veniam, quis nostrud exercitation ullamco laboris.<br><br>Duis aute irure dolor in reprehenderit in voluptate velit esse cillum dolore eu fugiat nulla pariatur.</p>
    <p class="txt">Lorem ipsum dolor sit amet, consectetur adipiscing elit, sed do eiusmod tempor incididunt ut labore et dolore magna aliqua. Ut enim ad minim veniam, quis nostrud exercitation ullamco laboris.<br><br>Duis aute irure dolor in reprehenderit in voluptate velit esse cillum dolore eu fugiat nulla pariatur.</p>
  </div>
  <footer class="foot">STEADFAST LINE LEADERSHIP<b>Page 24</b></footer>
</section>

<section class="slide">
  <h2 class="title">Column Text</h2><div class="mark"></div>
  <p class="abs red" style="left:24px;top:24px;font-size:4.6px">Lorem ipsum dolor sit amet, consectetur adipiscing elit</p>
  <p class="abs txt" style="left:24px;top:34px;width:174px">Lorem ipsum dolor sit amet, consectetur adipiscing elit, sed do eiusmod tempor incididunt ut labore et dolore magna aliqua. Ut enim ad minim veniam, quis nostrud exercitation ullamco laboris nisi ut aliquip ex ea commodo consequat. Duis aute irure dolor in reprehenderit in voluptate velit esse cillum dolore eu fugiat nulla pariatur.<br><br>Lorem ipsum dolor sit amet, consectetur adipiscing elit, sed do eiusmod tempor incididunt ut labore et dolore magna aliqua. Ut enim ad minim veniam, quis nostrud exercitation ullamco laboris nisi ut aliquip ex ea commodo consequat. Duis aute irure dolor in reprehenderit in voluptate velit esse.<br><br>Lorem ipsum dolor sit amet, consectetur adipiscing elit, sed do eiusmod tempor incididunt ut labore et dolore magna aliqua. Ut enim ad minim veniam, quis nostrud exercitation ullamco laboris nisi ut aliquip ex ea commodo consequat.</p>
  <footer class="foot">STEADFAST LINE LEADERSHIP<b>Page 25</b></footer>
</section>

<section class="slide">
  <h2 class="title">Editable Chart</h2><div class="mark"></div>
  <svg class="abs" style="left:16px;top:28px" width="70" height="70" viewBox="0 0 70 70">
    <g transform="rotate(-90 35 35)" fill="none" stroke-width="14">
      <circle cx="35" cy="35" r="26" stroke="var(--ink)" stroke-dasharray="40.8 163.4"/>
      <circle cx="35" cy="35" r="26" stroke="var(--red)" stroke-dasharray="65.3 163.4" stroke-dashoffset="-40.8"/>
      <circle cx="35" cy="35" r="26" stroke="var(--gold)" stroke-dasharray="57.2 163.4" stroke-dashoffset="-106.1"/>
    </g>
    <circle cx="35" cy="35" r="8" fill="var(--red)" stroke="var(--ink)" stroke-width="1"/>
    <g font-size="5" fill="#fff" font-family="Arimo, Arial, sans-serif"><text x="41" y="15">25%</text><text x="3" y="38">35%</text><text x="52" y="56">40%</text></g>
  </svg>
  <div class="dot" style="left:104px;top:36px;width:9px;height:9px"></div>
  <p class="abs txt" style="left:120px;top:35px;width:90px">Lorem ipsum dolor sit amet, consectetur adipiscing elit, sed do eiusmod tempor incididunt ut labore et dolore magna aliqua.</p>
  <div class="dot" style="left:104px;top:61px;width:9px;height:9px;background:var(--gold)"></div>
  <p class="abs txt" style="left:120px;top:60px;width:90px">Lorem ipsum dolor sit amet, consectetur adipiscing elit, sed do eiusmod tempor incididunt ut labore et dolore magna aliqua.</p>
  <div class="dot" style="left:104px;top:86px;width:9px;height:9px;background:var(--ink)"></div>
  <p class="abs txt" style="left:120px;top:85px;width:90px">Lorem ipsum dolor sit amet, consectetur adipiscing elit, sed do eiusmod tempor incididunt ut labore et dolore magna aliqua.</p>
  <footer class="foot">STEADFAST LINE LEADERSHIP<b>Page 26</b></footer>
</section>

<section class="slide">
  <h2 class="title">Editable Chart</h2><div class="mark"></div>
  <svg class="abs" style="left:20px;top:24px" width="190" height="62" viewBox="0 0 190 62">
    <g stroke="#e3e3e3" stroke-width=".4"><line x1="10" y1="4" x2="190" y2="4"/><line x1="10" y1="16" x2="190" y2="16"/><line x1="10" y1="28" x2="190" y2="28"/><line x1="10" y1="40" x2="190" y2="40"/><line x1="10" y1="52" x2="190" y2="52"/></g>
    <g font-size="2.8" fill="#555" font-family="Arimo, Arial, sans-serif"><text x="2" y="5">40</text><text x="2" y="17">30</text><text x="2" y="29">20</text><text x="2" y="41">10</text><text x="4" y="53">0</text>
      <text x="16" y="58">January</text><text x="53" y="58">February</text><text x="92" y="58">March</text><text x="128" y="58">April</text><text x="162" y="58">May</text></g>
    <g fill="var(--ink)"><rect x="16" y="12" width="5" height="40"/><rect x="52" y="14" width="5" height="38"/><rect x="88" y="10" width="5" height="42"/><rect x="124" y="22" width="5" height="30"/><rect x="160" y="20" width="5" height="32"/></g>
    <g fill="var(--red)"><rect x="21" y="14" width="5" height="38"/><rect x="57" y="22" width="5" height="30"/><rect x="93" y="18" width="5" height="34"/><rect x="129" y="24" width="5" height="28"/><rect x="165" y="18" width="5" height="34"/></g>
    <g fill="var(--gold)"><rect x="26" y="32" width="5" height="20"/><rect x="62" y="34" width="5" height="18"/><rect x="98" y="36" width="5" height="16"/><rect x="134" y="26" width="5" height="26"/><rect x="170" y="22" width="5" height="30"/></g>
  </svg>
  <div class="abs" style="left:26px;top:93px;display:grid;row-gap:3px">
    <p class="txt"><span class="key" style="background:var(--ink)"></span>Information Information Information</p>
    <p class="txt"><span class="key" style="background:var(--red)"></span>Information Information Information</p>
    <p class="txt"><span class="key" style="background:var(--gold)"></span>Information Information Information</p>
  </div>
  <p class="abs txt" style="left:112px;top:93px;width:90px">Lorem ipsum dolor sit amet, consectetur adipiscing elit, sed do eiusmod tempor incididunt ut labore et dolore magna aliqua.</p>
  <footer class="foot">STEADFAST LINE LEADERSHIP<b>Page 27</b></footer>
</section>

<section class="slide">
  <h2 class="title">Editable Chart</h2><div class="mark"></div>
  <svg class="abs" style="left:14px;top:24px" width="196" height="66" viewBox="0 0 196 66">
    <line x1="34" y1="2" x2="34" y2="62" stroke="#ccc" stroke-width=".5"/>
    <g font-size="2.8" fill="#555" font-family="Arimo, Arial, sans-serif"><text x="20" y="9">April</text><text x="18" y="24">March</text><text x="14" y="39">February</text><text x="16" y="55">January</text></g>
    <g fill="var(--ink)"><rect x="34" y="5" width="66" height="2.5"/><rect x="34" y="20" width="120" height="2.5"/><rect x="34" y="35" width="90" height="2.5"/><rect x="34" y="51" width="100" height="2.5"/></g>
    <g fill="var(--red)"><rect x="34" y="8" width="76" height="2.5"/><rect x="34" y="23" width="104" height="2.5"/><rect x="34" y="38" width="110" height="2.5"/><rect x="34" y="54" width="98" height="2.5"/></g>
    <g fill="var(--gold)"><rect x="34" y="11" width="60" height="2.5"/><rect x="34" y="26" width="72" height="2.5"/><rect x="34" y="41" width="84" height="2.5"/><rect x="34" y="57" width="104" height="2.5"/></g>
  </svg>
  <div class="abs" style="left:26px;top:95px;display:grid;row-gap:3px">
    <p class="txt"><span class="key" style="background:var(--ink)"></span>Information Information Information</p>
    <p class="txt"><span class="key" style="background:var(--red)"></span>Information Information Information</p>
    <p class="txt"><span class="key" style="background:var(--gold)"></span>Information Information Information</p>
  </div>
  <p class="abs txt" style="left:112px;top:95px;width:90px">Lorem ipsum dolor sit amet, consectetur adipiscing elit, sed do eiusmod tempor incididunt ut labore et dolore magna aliqua.</p>
  <footer class="foot">STEADFAST LINE LEADERSHIP<b>Page 28</b></footer>
</section>

<section class="slide">
  <h2 class="title">Editable Chart</h2><div class="mark"></div>
  <p class="abs red" style="left:24px;top:24px;font-size:4.4px">Lorem ipsum dolor sit amet, consectetur adipiscing elit</p>
  <p class="abs txt" style="left:24px;top:32px;width:180px">Lorem ipsum dolor sit amet, consectetur adipiscing elit, sed do eiusmod tempor incididunt ut labore et dolore magna aliqua. Ut enim ad minim veniam, quis nostrud exercitation ullamco laboris nisi ut aliquip.</p>
  <svg class="abs" style="left:0;top:46px" width="222" height="74" viewBox="0 0 222 74">
    <rect width="222" height="74" fill="var(--ink)"/>
    <g stroke="#333" stroke-width=".4"><line x1="20" y1="12" x2="215" y2="12"/><line x1="20" y1="26" x2="215" y2="26"/><line x1="20" y1="40" x2="215" y2="40"/><line x1="20" y1="54" x2="215" y2="54"/></g>
    <path d="M20 60 L50 56 L80 52 L110 46 L135 38 L150 18 L165 34 L180 42 L200 50 L215 56 L215 62 L20 62 Z" fill="var(--red)"/>
    <path d="M20 62 L50 60 L80 58 L110 54 L135 48 L150 32 L165 46 L180 52 L200 56 L215 60 L215 62 Z" fill="var(--gold)"/>
    <g font-size="2.6" fill="#aaa" font-family="Arimo, Arial, sans-serif"><text x="8" y="13">160</text><text x="8" y="27">120</text><text x="10" y="41">80</text><text x="10" y="55">40</text><text x="40" y="68">08/01/2018</text><text x="90" y="68">15/01/2018</text><text x="140" y="68">22/01/2018</text><text x="188" y="68">29/01/2018</text></g>
  </svg>
  <footer class="foot">STEADFAST LINE LEADERSHIP<b>Page 29</b></footer>
</section>

<section class="slide">
  <h2 class="title">Editable Chart</h2><div class="mark"></div>
  <svg class="abs" style="left:10px;top:28px" width="140" height="72" viewBox="0 0 140 72">
    <g stroke="#e3e3e3" stroke-width=".4"><line x1="16" y1="6" x2="138" y2="6"/><line x1="16" y1="20" x2="138" y2="20"/><line x1="16" y1="34" x2="138" y2="34"/><line x1="16" y1="48" x2="138" y2="48"/><line x1="16" y1="62" x2="138" y2="62"/></g>
    <g font-size="3" fill="#555" font-family="Arimo, Arial, sans-serif"><text x="4" y="7">137,5</text><text x="7" y="21">110</text><text x="7" y="35">82,5</text><text x="9" y="49">55</text><text x="7" y="63">27,5</text><text x="18" y="70">April</text><text x="40" y="70">May</text><text x="62" y="70">June</text><text x="84" y="70">July</text><text x="104" y="70">Aug</text><text x="124" y="70">Sept</text></g>
    <polyline points="20,52 42,42 64,36 86,24 108,14 128,20" fill="none" stroke="var(--ink)" stroke-width=".8"/>
    <polyline points="20,42 42,36 64,46 86,40 108,34 128,34" fill="none" stroke="var(--red)" stroke-width=".8"/>
    <g fill="var(--ink)"><circle cx="20" cy="52" r="1.2"/><circle cx="42" cy="42" r="1.2"/><circle cx="64" cy="36" r="1.2"/><circle cx="86" cy="24" r="1.2"/><circle cx="108" cy="14" r="1.2"/><circle cx="128" cy="20" r="1.2"/></g>
    <g fill="var(--red)"><circle cx="20" cy="42" r="1.2"/><circle cx="42" cy="36" r="1.2"/><circle cx="64" cy="46" r="1.2"/><circle cx="86" cy="40" r="1.2"/><circle cx="108" cy="34" r="1.2"/><circle cx="128" cy="34" r="1.2"/></g>
  </svg>
  <p class="abs txt" style="left:154px;top:38px;width:56px">Lorem ipsum dolor sit amet, consectetur adipiscing elit, sed do eiusmod tempor incididunt ut labore et dolore magna aliqua.</p>
  <p class="abs txt" style="left:154px;top:64px;width:56px">Lorem ipsum dolor sit amet, consectetur adipiscing elit, sed do eiusmod tempor incididunt ut labore et dolore magna aliqua.</p>
  <footer class="foot">STEADFAST LINE LEADERSHIP<b>Page 30</b></footer>
</section>

<section class="slide">
  <h2 class="title">Slide with image</h2><div class="mark"></div>
  <div class="photo" style="left:0;top:20px;width:222px;height:58px;background:linear-gradient(90deg,#cfcfcf,#f1f1f1 45%,#bdb6ad)" role="img" aria-label="Handshake over a desk with a newspaper and phone"></div>
  <div class="abs" style="left:50px;top:72px;width:12px;height:12px;background:var(--ink)"></div>
  <div class="abs" style="left:116px;top:72px;width:12px;height:12px;background:var(--red)"></div>
  <div class="abs" style="left:176px;top:72px;width:12px;height:12px;background:var(--gold)"></div>
  <p class="abs txt" style="left:28px;top:90px;width:58px;text-align:center">Lorem ipsum dolor sit amet, consectetur adipiscing elit, sed do eiusmod tempor incididunt ut labore et dolore magna aliqua.</p>
  <p class="abs txt" style="left:92px;top:90px;width:58px;text-align:center">Lorem ipsum dolor sit amet, consectetur adipiscing elit, sed do eiusmod tempor incididunt ut labore et dolore magna aliqua.</p>
  <p class="abs txt" style="left:154px;top:90px;width:58px;text-align:center">Lorem ipsum dolor sit amet, consectetur adipiscing elit, sed do eiusmod tempor incididunt ut labore et dolore magna aliqua.</p>
  <footer class="foot">STEADFAST LINE LEADERSHIP<b>Page 31</b></footer>
</section>

<section class="slide">
  <h2 class="title">Slide with image</h2><div class="mark"></div>
  <div class="photo" style="left:0;top:24px;width:222px;height:90px;background:linear-gradient(110deg,#8d8478,#c9c2b6 45%,#6e665c)" role="img" aria-label="Empty conference room with large windows"></div>
  <div class="abs" style="left:20px;top:24px;width:44px;height:90px;background:rgba(22,22,22,.92)"></div>
  <p class="abs txt" style="left:26px;top:56px;width:34px;color:var(--soft)">Lorem ipsum dolor sit amet, consectetur adipiscing elit, sed do eiusmod tempor incididunt ut labore et dolore magna aliqua.</p>
  <footer class="foot">STEADFAST LINE LEADERSHIP<b>Page 32</b></footer>
</section>

<section class="slide">
  <h2 class="title">Slide with image</h2><div class="mark"></div>
  <div class="photo" style="left:10px;top:26px;width:110px;height:88px;background:linear-gradient(135deg,#9a9a9a,#5e5e5e 55%,#3a3a3a)" role="img" aria-label="Business team meeting around a table"></div>
  <div class="abs" style="left:10px;top:54px;width:22px;height:22px;background:var(--red)"></div>
  <div class="abs" style="left:32px;top:54px;width:22px;height:22px;background:var(--red-deep)"></div>
  <p class="abs red" style="left:138px;top:28px;font-size:4.6px">LOREM IPSUM</p>
  <p class="abs txt" style="left:138px;top:36px;width:70px">Lorem ipsum dolor sit amet, consectetur adipiscing elit, sed do eiusmod tempor incididunt ut labore et dolore magna aliqua. Ut enim ad minim veniam, quis nostrud exercitation ullamco laboris nisi ut aliquip ex ea commodo consequat.<br><br>Duis aute irure dolor in reprehenderit in voluptate velit esse cillum dolore eu fugiat nulla pariatur. Excepteur sint occaecat cupidatat non proident, sunt in culpa qui officia deserunt mollit anim id est laborum.</p>
  <footer class="foot">STEADFAST LINE LEADERSHIP<b>Page 33</b></footer>
</section>

<section class="slide">
  <h2 class="title">Slide with image</h2><div class="mark"></div>
  <div class="photo" style="left:16px;top:26px;width:98px;height:46px;background:linear-gradient(135deg,#2c3a52,#6d86a8)" role="img" aria-label="Businessman touching a digital network display"></div>
  <div class="abs" style="left:114px;top:26px;width:92px;height:30px;background:var(--red)"></div>
  <p class="abs txt" style="left:120px;top:30px;width:82px;color:#fff">Lorem ipsum dolor sit amet, consectetur adipiscing elit, sed do eiusmod tempor incididunt ut labore et dolore magna aliqua.</p>
  <div class="abs" style="left:16px;top:78px;width:98px;height:30px;background:var(--ink)"></div>
  <p class="abs txt" style="left:22px;top:84px;width:84px;color:var(--soft)">Lorem ipsum dolor sit amet, consectetur adipiscing elit, sed do eiusmod tempor incididunt ut labore et dolore magna aliqua.</p>
  <div class="photo" style="left:114px;top:72px;width:92px;height:46px;background:linear-gradient(135deg,#3f6a96,#a8c2de)" role="img" aria-label="Hands using a tablet with network icons"></div>
  <footer class="foot">STEADFAST LINE LEADERSHIP<b>Page 34</b></footer>
</section>

<section class="slide dark">
  <p class="abs brand" style="left:0;width:222px;top:37px;font-size:8px">CONTACT US</p>
  <p class="abs txt" style="left:0;width:222px;top:51px;text-align:center;color:#ddd">Steadfast Line Leadership Institute</p>
  <svg class="abs" style="left:80px;top:61px" width="8" height="32" viewBox="0 0 8 32" fill="#ddd">
    <rect x="1" y="1" width="6" height="6"/>
    <path d="M2 12 q1-1 2 0 l1 2 q-1 1 0 2 l1 1 q1-1 2 0 l-1 2 q-4 0-5-5z"/>
    <rect x="1" y="25" width="6" height="4"/><path d="M1 25 l3 2 l3-2" stroke="#161616" stroke-width=".5" fill="none"/>
  </svg>
  <p class="abs txt" style="left:92px;top:61px;width:60px;color:#ddd">410 Harbor Lane<br>Fairview, TX 75000</p>
  <p class="abs txt" style="left:92px;top:73px;color:#ddd">555.014.2700</p>
  <p class="abs txt" style="left:92px;top:86px;color:#ddd">hello@steadfastline.com</p>
</section>

</main>
</body>
</html>
```